E learning Platform for privacy

Current website is as below and its more of a shell.
I need someone to take the text and content and design it properly.
https://study.vornaquill.com/

After that, design has to be implemented with elementor and wordpress
https://elementor.com/

```html
<!DOCTYPE html>
<html lang="en">
<head>
<meta charset="utf-8">
<title>Vornaquill Learning Centre</title>
<link href="https://fonts.googleapis.com/css2?family=Roboto:wght@300;400;500;700&family=Open+Sans:wght@400;600;700&display=swap" rel="stylesheet">
<style>
:root{
  --orange:#f5821f;
  --orange-deep:#e2461b;
  --red:#d8381e;
  --ink:#222;
  --text:#4a4a4a;
  --muted:#777;
  --light:#f2f2f2;
  --grey-top:#6b6b6b;
  --grey-bot:#3a3a3a;
  --footer:#2a2b2d;
  --white:#fff;
}
*{box-sizing:border-box;margin:0;padding:0}
html,body{width:1200px;height:4035px;overflow:hidden;background:var(--white)}
body{font-family:"Roboto",Arial,sans-serif;color:var(--ink);position:relative}
.small{font-family:"Open Sans",Arial,sans-serif}

/* header */
.site-header{height:103px;display:flex;align-items:center;padding:0 80px;border-bottom:1px solid #eee}
.brand{display:flex;align-items:center;gap:10px;width:330px}
.brand-mark{width:16px;height:16px;background:var(--orange-deep)}
.brand-name{font-size:30px;font-weight:700;color:var(--orange-deep);letter-spacing:1px}
.main-nav{display:flex;gap:38px;font-size:13px;font-weight:700;letter-spacing:.3px;margin-left:80px}
.main-nav a{color:var(--ink);text-decoration:none;position:relative}
.main-nav a.active{color:var(--orange)}
.main-nav a.active::before{content:"";position:absolute;left:12px;top:-20px;width:18px;height:12px;border-top:2px solid var(--ink);border-bottom:2px solid var(--ink)}
.auth{margin-left:auto;display:flex;gap:8px}
.btn-pill{height:38px;border-radius:19px;padding:0 30px;display:flex;align-items:center;font-size:12px;font-weight:700}
.btn-outline{border:1.5px solid #555;color:#444}
.btn-fill{background:var(--orange);color:var(--white)}

/* hero */
.hero{height:617px;position:relative;background:linear-gradient(120deg,#6e6259 0%,#a79888 40%,#5c4f48 75%,#3d3a3e 100%)}
.hero-card{position:absolute;left:125px;top:164px;width:423px;height:268px;background:rgba(245,130,31,.93);border-radius:34px;padding:26px 56px;color:var(--white)}
.hero-card h1{font-size:39px;font-weight:700;line-height:1.06}
.hero-card p{font-size:20px;font-weight:300;line-height:1.25;margin-top:14px}
.hero-btn{display:inline-flex;margin-top:22px;border:2px solid var(--white);border-radius:24px;height:46px;padding:0 36px;align-items:center;font-size:14px;font-weight:700}
.dots{position:absolute;left:553px;top:570px;display:flex;gap:8px}
.dots i{width:13px;height:13px;border-radius:50%;background:var(--white)}
.dots i:first-child{background:transparent;border:2px solid var(--white)}

/* about */
.about{height:573px;text-align:center;padding-top:80px}
.section-title{font-size:28px;font-weight:700;color:var(--ink)}
.about p{font-size:17px;color:var(--text);line-height:1.6;width:940px;margin:22px auto 0;font-weight:300}
.stats{display:flex;gap:22px;justify-content:center;margin-top:88px}
.stat{width:302px;height:167px;color:var(--white);position:relative;padding-top:68px}
.stat-students{background:linear-gradient(var(--orange),#f56d1a)}
.stat-lessons{background:linear-gradient(var(--grey-top),var(--grey-bot))}
.stat-videos{background:linear-gradient(#ee5a25,var(--red))}
.stat-badge{position:absolute;left:50%;top:-58px;margin-left:-51px;width:102px;height:102px;border-radius:50%;background:var(--white);border:2px solid currentColor;display:flex;align-items:center;justify-content:center}
.stat-students .stat-badge{color:var(--orange)}
.stat-lessons .stat-badge{color:#555}
.stat-videos .stat-badge{color:var(--red)}
.stat-label{font-size:17px;font-weight:700;letter-spacing:.3px}
.stat-value{font-size:44px;font-weight:700;margin-top:2px}

/* featured */
.featured{height:632px;background:var(--light);text-align:center;padding-top:52px}
.course-grid{display:flex;gap:20px;justify-content:center;margin-top:38px}
.course{width:305px;height:372px;background:var(--white);border:1px solid #ddd;text-align:left}
.course-media{height:203px}
.m1{background:linear-gradient(135deg,#15207a,#3c5ad8 60%,#1a2a90)}
.m2{background:linear-gradient(135deg,#0e2838,#3b7fa0 55%,#4a4a50)}
.m3{background:linear-gradient(135deg,#5d6f86,#a6b6c8 55%,#2f3f55)}
.course-body{padding:30px 26px 0}
.course h3{font-size:18px;font-weight:500;color:#333}
.course p{font-size:13px;color:#666;line-height:1.5;margin-top:12px}
.meta{display:flex;justify-content:space-between;font-size:12.5px;color:#555;margin-top:16px}
.meta span::before{content:"";display:inline-block;width:11px;height:11px;background:var(--orange);margin-right:5px;vertical-align:-1px;border-radius:2px}
.meta span.author::before{border-radius:50% 50% 2px 2px}
.view-all{display:inline-flex;margin-top:38px;height:50px;width:182px;border:2px solid var(--orange);border-radius:25px;align-items:center;justify-content:center;color:var(--orange);font-size:15px;font-weight:700}

/* why */
.why{height:695px;padding-top:78px;text-align:center}
.why-grid{display:grid;grid-template-columns:repeat(3,340px);column-gap:0;row-gap:50px;margin:70px 0 0 147px;text-align:left}
.why-item svg{display:block;margin-bottom:12px}
.why-item h4{font-size:15.5px;font-weight:700;color:#222;line-height:1.3;width:260px}
.why-item p{font-size:13.5px;color:#333;line-height:1.45;margin-top:12px;width:260px}

/* testimonial */
.testimonial{height:423px;background:linear-gradient(100deg,var(--orange-deep),var(--orange));color:var(--white);position:relative}
.testimonial h2{font-size:33px;font-weight:700;position:absolute;left:0;right:0;text-align:center;top:68px}
.avatar-ring{position:absolute;left:215px;top:134px;width:190px;height:190px;border-radius:50%;border:2px solid rgba(255,255,255,.85);padding:10px}
.avatar{width:100%;height:100%;border-radius:50%;background:radial-gradient(circle at 50% 40%,#c99a82,#6f4a3a 70%)}
.quote-mark{position:absolute;left:405px;top:150px;font-size:90px;font-weight:700;line-height:1;font-family:Georgia,serif}
.quote{position:absolute;left:470px;top:148px;width:540px;font-size:20px;font-weight:300;line-height:1.75}
.by{position:absolute;left:471px;top:262px;font-size:20px;font-weight:700}
.company{position:absolute;left:471px;top:292px;font-size:13px;font-weight:700}
.arrow{position:absolute;top:190px}

/* blogs */
.blogs{height:592px;padding:72px 0 0 133px}
.blogs h2{font-size:29px;font-weight:500}
.blog-grid{display:flex;gap:33px;margin-top:28px;margin-left:-6px}
.blog{width:290px;height:360px;background:var(--white);box-shadow:0 2px 10px rgba(0,0,0,.12)}
.blog-media{height:170px}
.b1{background:linear-gradient(135deg,#3f4a52,#8fa3a8 55%,#d6dcdc)}
.b2{background:linear-gradient(135deg,#5a5250,#b3aaa5 55%,#6b5f5b)}
.b3{background:linear-gradient(135deg,#7b8a94,#c7cfd3 50%,#b3373d 80%)}
.blog-body{padding:20px 22px 0}
.blog-head{display:flex;gap:12px}
.date{width:40px;height:46px;background:#e7e7e7;text-align:center;padding-top:3px;color:#333}
.date b{display:block;font-size:20px;font-weight:500;line-height:1}
.date small{font-size:13px}
.blog h3{font-size:17px;font-weight:400;color:var(--orange-deep);line-height:1.3}
.blog p{font-size:12px;color:#777;line-height:1.45;margin-top:14px}
.read{font-size:12px;font-weight:700;color:#222;margin-top:14px;display:block}

/* footer */
.site-footer{height:400px;background:var(--footer);color:#ddd;position:relative}
.f-brand{position:absolute;left:140px;top:70px;display:flex;align-items:center;gap:12px}
.f-brand .brand-mark{background:var(--white)}
.f-brand .brand-name{color:var(--white)}
.f-about{position:absolute;left:140px;top:150px;font-size:13px;color:#999;line-height:1.65;width:230px}
.chat{position:absolute;left:137px;top:213px;width:182px;height:42px;border-radius:21px;background:var(--orange);color:var(--white);display:flex;align-items:center;justify-content:center;gap:8px;font-size:15px;font-weight:700}
.f-col{position:absolute;top:72px}
.f-col h5{font-size:15px;font-weight:700;color:var(--white);letter-spacing:.3px}
.f-col ul{list-style:none;margin-top:14px;font-size:13.5px;line-height:23px;color:#ccc}
.f-links{left:470px}
.f-sign{left:640px}
.f-sign p{font-size:12px;color:#ccc;margin-top:22px}
.email{margin-top:12px;margin-left:-4px;width:258px;height:38px;border-radius:19px;background:var(--white);color:#555;font-size:12px;padding:0 22px;display:flex;align-items:center}
.subscribe{margin-top:12px;width:118px;height:36px;border-radius:18px;background:var(--orange);color:var(--white);font-size:12px;font-weight:700;display:flex;align-items:center;justify-content:center}
.f-social{left:955px}
.f-social ul{line-height:33px;margin-top:8px}
.f-social li::before{content:"";display:inline-block;width:20px;height:20px;border:1.5px solid #ccc;border-radius:50%;margin-right:9px;vertical-align:-5px}
.f-bottom{position:absolute;left:0;right:0;top:316px;height:84px;border-top:1px solid #3b3c3f;display:flex;align-items:center;padding:0 142px;font-size:11.5px;color:#ccc}
.powered{margin-left:auto;display:flex;align-items:center;gap:14px}
.powered b{font-size:19px;color:var(--orange-deep);font-weight:700}
.powered em{font-style:normal;font-size:14px;color:#5a8fd6;border-left:1px solid #666;padding-left:12px}
</style>
</head>
<body>

<header class="site-header">
  <div class="brand"><span class="brand-mark"></span><span class="brand-name">Vornaquill</span></div>
  <nav class="main-nav">
    <a class="active" href="#">HOME</a><a href="#">ABOUT</a><a href="#">BLOGS</a><a href="#">COURSES</a><a href="#">CONTACT</a>
  </nav>
  <div class="auth"><span class="btn-pill btn-outline">SIGN IN</span><span class="btn-pill btn-fill">REGISTER</span></div>
</header>

<section class="hero" role="img" aria-label="Photo of students studying together around a laptop">
  <div class="hero-card">
    <h1>Data Privacy Excellence</h1>
    <p>Largest online e-learning resource for data protection &amp; privacy</p>
    <span class="hero-btn">GET STATED</span>
  </div>
  <div class="dots"><i></i><i></i><i></i><i></i></div>
</section>

<section class="about">
  <h2 class="section-title">About Vornaquill Learning Centre</h2>
  <p>Our mission at the Vornaquill Learning Centre is to provide business and job opportunities, as well as to enhance personal and career advancement for data protection / privacy professionals.</p>
  <div class="stats">
    <div class="stat stat-students">
      <div class="stat-badge"><svg width="56" height="44" viewBox="0 0 56 44" fill="none" stroke="currentColor" stroke-width="2"><path d="M2 14 28 3l26 11-26 11z"/><path d="M12 19v12c8 7 24 7 32 0V19"/><path d="M50 16v14"/></svg></div>
      <div class="stat-label">ENROLLED STUDENTS</div><div class="stat-value">6,375</div>
    </div>
    <div class="stat stat-lessons">
      <div class="stat-badge"><svg width="48" height="52" viewBox="0 0 48 52" fill="none" stroke="currentColor" stroke-width="2"><rect x="6" y="3" width="30" height="42"/><path d="M12 12h18M12 18h18M12 24h12"/><circle cx="34" cy="38" r="8"/><circle cx="34" cy="38" r="3"/></svg></div>
      <div class="stat-label">LESSONS</div><div class="stat-value">114</div>
    </div>
    <div class="stat stat-videos">
      <div class="stat-badge"><svg width="54" height="54" viewBox="0 0 54 54" fill="none" stroke="currentColor" stroke-width="2"><circle cx="27" cy="27" r="23"/><path d="M21 16v22l17-11z"/></svg></div>
      <div class="stat-label">VIDEOS</div><div class="stat-value">169</div>
    </div>
  </div>
</section>

<section class="featured">
  <h2 class="section-title">Featured Courses</h2>
  <div class="course-grid">
    <article class="course">
      <div class="course-media m1" role="img" aria-label="Illustration of a padlock on a blue circuit board"></div>
      <div class="course-body small"><h3>How to Scale Social Impact</h3><p>Lorem ipsum dolor sit amet consectetuer adipiscing elit Nam cursus Morbi</p><div class="meta"><span>19 Dec, 2019</span><span class="author">Mr. Edwin Marlow</span></div></div>
    </article>
    <article class="course">
      <div class="course-media m2" role="img" aria-label="Hands typing on a keyboard with security icons"></div>
      <div class="course-body small"><h3>Lyra Demonstration Course</h3><p>Lorem ipsum dolor sit amet consectetuer adipiscing elit Nam cursus Morbi</p><div class="meta"><span>19 Dec, 2019</span><span class="author">Mr. Edwin Marlow</span></div></div>
    </article>
    <article class="course">
      <div class="course-media m3" role="img" aria-label="Person touching a digital security interface"></div>
      <div class="course-body small"><h3>How to Scale Social Impact</h3><p>Lorem ipsum dolor sit amet consectetuer adipiscing elit Nam cursus Morbi</p><div class="meta"><span>19 Dec, 2019</span><span class="author">Mr. Edwin Marlow</span></div></div>
    </article>
  </div>
  <span class="view-all">VIEW ALL</span>
</section>

<section class="why">
  <h2 class="section-title" style="font-size:25px">Why the (Vornaquill) Learning Centre?</h2>
  <div class="why-grid small">
    <div class="why-item">
      <svg width="64" height="54" viewBox="0 0 64 54" fill="none" stroke="#e2461b" stroke-width="2"><circle cx="8" cy="6" r="4"/><path d="M12 6h34a8 8 0 0 1 0 16H18a8 8 0 0 0 0 16h32"/><circle cx="54" cy="38" r="4"/><path d="M8 44h40"/></svg>
      <h4>Comprehensive Roadmap</h4><p>Our objective is to provide a comprehensive competency roadmap, instead of one-off courses, whether you are a new or experienced</p>
    </div>
    <div class="why-item">
      <svg width="64" height="54" viewBox="0 0 64 54" fill="none" stroke="#e2461b" stroke-width="2"><rect x="6" y="12" width="52" height="36" rx="3"/><path d="M24 12V6h16v6M6 26h52M28 26v6h8v-6"/></svg>
      <h4>Operational Perspective</h4><p>We cover a broad range of data protection topics from both a legal and operational perspective, covering multiple jurisdictions</p>
    </div>
    <div class="why-item">
      <svg width="64" height="54" viewBox="0 0 64 54" fill="none" stroke="#e2461b" stroke-width="2"><path d="M20 4h24v14a12 12 0 0 1-24 0z"/><path d="M20 8h-8a8 8 0 0 0 8 12M44 8h8a8 8 0 0 1-8 12M32 30v10M22 48h20l-3-8H25z"/></svg>
      <h4>Academic &amp; International Certification</h4><p>We partner with prominent universities in the region as well as international certification bodies</p>
    </div>
    <div class="why-item">
      <svg width="64" height="54" viewBox="0 0 64 54" fill="none" stroke="#e2461b" stroke-width="2"><circle cx="44" cy="8" r="5"/><circle cx="30" cy="20" r="5"/><circle cx="12" cy="40" r="5"/><circle cx="34" cy="44" r="5"/><path d="M34 17l6-6M26 24 15 36M17 41l12 2M31 25l2 14"/></svg>
      <h4>Network with other peers</h4><p>Participate in our online communities and discussion rooms and your network with other like-minded course</p>
    </div>
    <div class="why-item">
      <svg width="64" height="54" viewBox="0 0 64 54" fill="none" stroke="#e2461b" stroke-width="2"><rect x="8" y="8" width="38" height="26" rx="2"/><path d="M20 8V3h14v5M8 18h38"/><path d="M36 40l10-10 10 10-10 10z"/></svg>
      <h4>Business and Job Opportunities</h4><p>Collaborate with other professionals on potential business opportunities whether it relates to consultancy</p>
    </div>
    <div class="why-item">
      <svg width="64" height="54" viewBox="0 0 64 54" fill="none" stroke="#e2461b" stroke-width="2"><path d="M8 14 32 4l24 10v26L32 50 8 40z"/><path d="M8 14l24 10 24-10M32 24v26M20 9l24 10v8"/></svg>
      <h4>Modular Approach &amp; Flexibility</h4><p>All our courses are modular in nature to cater to the busy professional, meaning that you can take</p>
    </div>
  </div>
</section>

<section class="testimonial">
  <h2>What People Say</h2>
  <svg class="arrow" style="left:122px" width="28" height="54" viewBox="0 0 28 54" fill="none" stroke="#fff" stroke-width="2.5"><path d="M26 2 3 27l23 25"/></svg>
  <div class="avatar-ring"><div class="avatar" role="img" aria-label="Portrait photo of a smiling client"></div></div>
  <div class="quote-mark">“</div>
  <p class="quote">Fusce tellus Sed metus augue convallis et vehicula ut pulvinar eu ante Integer orci tellus tristique vitae consequat nec porta vel lectus Nulla sit amet diamaliquam</p>
  <div class="by">By Author Name</div>
  <div class="company">Company Name</div>
  <svg class="arrow" style="left:1066px" width="28" height="54" viewBox="0 0 28 54" fill="none" stroke="#fff" stroke-width="2.5"><path d="M2 2l23 25L2 52"/></svg>
</section>

<section class="blogs">
  <h2>Latest Blogs</h2>
  <div class="blog-grid">
    <article class="blog">
      <div class="blog-media b1" role="img" aria-label="Man in glasses working at a desk"></div>
      <div class="blog-body small"><div class="blog-head"><div class="date"><b>18</b><small>JAN</small></div><h3>Pellentesque faucibus Ut accumsan ultric</h3></div><p>Duis quam Nam eget lacus Aliquam erat volutpat Quisque dignissim congue leo Mauris vel lacus vitae felis vestibulum</p><span class="read">READ MORE</span></div>
    </article>
    <article class="blog">
      <div class="blog-media b2" role="img" aria-label="Hands typing on a laptop"></div>
      <div class="blog-body small"><div class="blog-head"><div class="date"><b>10</b><small>JAN</small></div><h3>Pellentesque faucibus Ut accumsan ultric</h3></div><p>Duis quam Nam eget lacus Aliquam erat volutpat Quisque dignissim congue leo Mauris vel lacus vitae felis vestibulum</p><span class="read">READ MORE</span></div>
    </article>
    <article class="blog">
      <div class="blog-media b3" role="img" aria-label="Students studying together with a laptop"></div>
      <div class="blog-body small"><div class="blog-head"><div class="date"><b>15</b><small>JAN</small></div><h3>Pellentesque faucibus Ut accumsan ultric</h3></div><p>Duis quam Nam eget lacus Aliquam erat volutpat Quisque dignissim congue leo Mauris vel lacus vitae felis vestibulum</p><span class="read">READ MORE</span></div>
    </article>
  </div>
</section>

<footer class="site-footer small">
  <div class="f-brand"><span class="brand-mark"></span><span class="brand-name" style="font-family:Roboto,Arial,sans-serif">Vornaquill</span></div>
  <p class="f-about">Lorem ipsum dolor sit amet consectetuer adipiscing elit</p>
  <div class="chat"><svg width="18" height="16" viewBox="0 0 18 16" fill="none" stroke="#fff" stroke-width="1.8"><path d="M2 2h14v9H7l-4 3v-3H2z"/></svg>CHAT NOW</div>
  <div class="f-col f-links"><h5>QUICK LINKS</h5><ul><li>About</li><li>Courses</li><li>Blogs</li><li>Testimonials</li><li>Why Us</li><li>Contact</li></ul></div>
  <div class="f-col f-sign"><h5>SIGN UP TO RECEIVE EMAIL</h5><p>Excepteur sint occaecat cupidatat n</p><div class="email">Enter Email</div><div class="subscribe">SUBSCRIBE</div></div>
  <div class="f-col f-social"><h5>SOCIAL</h5><ul><li>Friendbook</li><li>Chirper</li><li>Searchly+</li><li>Vidstream</li></ul></div>
  <div class="f-bottom"><span>Copyright © 2020 All right reserved</span><div class="powered"><span>Powered by</span><b>Corvell</b><em>OpenLyra</em></div></div>
</footer>

</body>
</html>
```